Facebook Header Design Project.

I'm supplying white and colored logos. The Facebook page already exists. URL = https://www.brindlepost.example/quillarc.studio The design should not be based on what's already there. Consider mobile implications of the design. This Design will form the designs of other social media headers. QuillArc is a web design | digital marketing company.

Target Market(s)

People interested in web design | digital marketing services.

Industry/Entity Type

QuillArc is a web design | digital marketing company. That should be clear in the design.

Colors
0054AA
0677BA
7BADD7
CADEEF
E8F1F8

Requirements
Must have
• Logo. Use Facebook header image dimension.
Nice to have
• Use a color scheme like the logo and feel free to add a color or two from the other side of the color whee.

```html
<!DOCTYPE html>
<html lang="en">
<head>
<meta charset="utf-8">
<title>QuillArc – Social Header</title>
<link rel="stylesheet" href="https://fonts.googleapis.com/css2?family=Montserrat:wght@300;400;500;700&display=swap">
<style>
  :root {
    --brand-deep: #1d3f91;
    --brand-blue: #0054aa;
    --brand-mid: #1a7cc0;
    --brand-sky: #7badd7;
    --brand-mist: #cadeef;
    --canvas-bg: #f6f6f8;
    --band-soft: #eceef5;
    --frame-edge: #c9cfe4;
    --photo-dark: #06182c;
    --photo-mid: #0b3a5c;
    --photo-glow: #3ec6e6;
  }
  html, body {
    margin: 0;
    padding: 0;
    overflow: hidden;
    background: #ffffff;
  }
  .header {
    position: relative;
    width: 1200px;
    height: 457px;
    overflow: hidden;
    background: var(--canvas-bg);
    font-family: "Montserrat", Arial, sans-serif;
  }
  .header__backdrop {
    position: absolute;
    inset: 0;
  }
  .brand {
    position: absolute;
    left: 52px;
    top: 52px;
    display: flex;
    align-items: center;
    gap: 12px;
  }
  .brand__dot {
    width: 22px;
    height: 22px;
    border-radius: 50%;
    background: var(--brand-blue);
  }
  .brand__name {
    font-size: 52px;
    font-weight: 700;
    color: var(--brand-blue);
    letter-spacing: -0.5px;
    line-height: 1;
  }
  .tagline-frame {
    position: absolute;
    left: 0;
    top: 0;
  }
  .tagline {
    position: absolute;
    left: 53px;
    top: 180px;
    margin: 0;
    font-weight: 400;
    line-height: 43px;
    font-size: 29px;
    color: var(--brand-deep);
  }
  .tagline__lead {
    display: block;
    font-weight: 300;
    color: var(--brand-mid);
  }
  .tagline__line {
    display: block;
  }
  .contact {
    position: absolute;
    left: 53px;
    color: var(--brand-deep);
    font-weight: 400;
  }
  .contact--address {
    top: 341px;
    font-size: 20px;
    letter-spacing: 0.4px;
  }
  .contact-row {
    position: absolute;
    left: 45px;
    top: 386px;
    display: flex;
    align-items: center;
    font-size: 22px;
    color: var(--brand-deep);
  }
  .contact-row__item {
    display: flex;
    align-items: center;
    gap: 7px;
    margin-right: 16px;
  }
  .icon {
    width: 27px;
    height: 27px;
    display: block;
  }
</style>
</head>
<body>
<div class="header">

  <svg class="header__backdrop" width="1200" height="457" viewBox="0 0 1200 457">
    <defs>
      <linearGradient id="photoTone" x1="0" y1="0" x2="1" y2="1">
        <stop offset="0" stop-color="#0a2a44"/>
        <stop offset="0.35" stop-color="#0e4d73"/>
        <stop offset="0.6" stop-color="#1a8bb5"/>
        <stop offset="0.85" stop-color="#0b3558"/>
        <stop offset="1" stop-color="#06182c"/>
      </linearGradient>
      <radialGradient id="photoGlow" cx="0.35" cy="0.6" r="0.5">
        <stop offset="0" stop-color="#3ec6e6" stop-opacity="0.55"/>
        <stop offset="1" stop-color="#3ec6e6" stop-opacity="0"/>
      </radialGradient>
      <linearGradient id="softSweep" x1="0" y1="0" x2="1" y2="0">
        <stop offset="0" stop-color="#ffffff" stop-opacity="0"/>
        <stop offset="1" stop-color="#e4e7f1"/>
      </linearGradient>
    </defs>

    <!-- soft diagonal background bands -->
    <polygon points="480,0 760,0 610,457 330,457" fill="#ffffff" opacity="0.7"/>
    <polygon points="560,0 800,0 700,228 600,457 470,457" fill="url(#softSweep)" opacity="0.8"/>

    <!-- light frame around photo -->
    <path d="M742,0 L1200,0 L1200,457 L742,457 L652,250 Q643,228 652,206 Z" fill="var(--frame-edge)" opacity="0.75"/>

    <!-- photo area -->
    <g role="img" aria-label="Photo: businessman in a suit touching a tablet, overlaid with a glowing blue digital city grid">
      <path d="M762,0 L1200,0 L1200,457 L762,457 L672,250 Q663,228 672,206 Z" fill="url(#photoTone)"/>
      <path d="M762,0 L1200,0 L1200,457 L762,457 L672,250 Q663,228 672,206 Z" fill="url(#photoGlow)"/>
    </g>
  </svg>

  <div class="brand">
    <span class="brand__dot"></span>
    <span class="brand__name">QuillArc</span>
  </div>

  <svg class="tagline-frame" width="700" height="340" viewBox="0 0 700 340" aria-hidden="true">
    <polyline points="157,168 637,168 518,320 7,320 51,256"
              fill="none" stroke="var(--brand-blue)" stroke-width="3.5" stroke-linejoin="miter"/>
  </svg>

  <h1 class="tagline">
    <span class="tagline__lead">Complete solutions for</span>
    <span class="tagline__line">Digital Marketing, Graphics Design</span>
    <span class="tagline__line">&amp; Web Development</span>
  </h1>

  <p class="contact contact--address" style="margin:0">48 North Alder Lane #512 60417</p>

  <div class="contact-row">
    <span class="contact-row__item">
      <svg class="icon" viewBox="0 0 28 28" aria-hidden="true">
        <circle cx="14" cy="14" r="14" fill="var(--brand-deep)"/>
        <path d="M9.5 7.5c.6-.6 1.5-.5 2 .1l1.6 2.1c.4.6.4 1.4-.1 1.9l-1 1c.8 1.7 2.1 3 3.8 3.8l1-1c.5-.5 1.3-.5 1.9-.1l2.1 1.6c.6.5.7 1.4.1 2l-1.1 1.1c-.9.9-2.3 1.1-3.4.5-3.2-1.6-5.8-4.2-7.4-7.4-.6-1.1-.4-2.5.5-3.4z" fill="#ffffff"/>
      </svg>
      +1 555-018-2746
    </span>
    <span class="contact-row__item">
      <svg class="icon" viewBox="0 0 28 28" aria-hidden="true">
        <circle cx="14" cy="14" r="14" fill="var(--brand-deep)"/>
        <rect x="7.5" y="8" width="13" height="9" rx="1" fill="none" stroke="#ffffff" stroke-width="1.8"/>
        <rect x="12.5" y="17" width="3" height="2.5" fill="#ffffff"/>
        <rect x="10" y="19.3" width="8" height="1.6" rx="0.5" fill="#ffffff"/>
      </svg>
      www.quillarc.example
    </span>
  </div>

</div>
</body>
</html>
```